Business Card Design

New business card design

Target Market(s)

Residential & Commercial Property Managers

Industry/Entity Type

Plumbing Services

Contact Information for Business Card

Name - Rowan Keddle, title - Director, Phone Number - 0431 286 517, email - rowan@tbk-plumbing.com.au, Company ABN - 73 215 904 386,

Font styles to use
Sans Serif

Colors
0054AA
0677BA
7BADD7
CADEEF
E8F1F8

```html
<!DOCTYPE html>
<html lang="en">
<head>
<meta charset="utf-8">
<title>TBK Plumbing Services – Business Card</title>
<link rel="stylesheet" href="https://fonts.googleapis.com/css2?family=Montserrat:wght@400;500;600;700&display=swap">
<style>
  :root {
    --stage: #222222;
    --card-white: #ffffff;
    --card-navy: #1d232b;
    --ink: #1c2530;
    --ink-soft: #6b625a;
    --blue-deep: #0054AA;
    --blue: #0677BA;
    --blue-bright: #29a8e0;
    --blue-mid: #7BADD7;
    --blue-pale: #CADEEF;
    --blue-mist: #E8F1F8;
  }
  * { box-sizing: border-box; margin: 0; padding: 0; }
  html, body { width: 1200px; height: 780px; overflow: hidden; }
  body {
    background: var(--stage);
    font-family: "Montserrat", sans-serif;
    position: relative;
  }
  .card {
    position: absolute;
    top: 235px;
    width: 540px;
    height: 310px;
    overflow: hidden;
  }
  .card--front { left: 30px; background: var(--card-white); }
  .card--back  { left: 630px; background: var(--card-navy); }

  .corner-panel {
    position: absolute;
    left: 0;
    bottom: 0;
    width: 260px;
    height: 140px;
    background: var(--blue-mist);
  }

  .brand {
    position: absolute;
    display: flex;
    align-items: center;
    gap: 10px;
    font-weight: 500;
    white-space: nowrap;
  }
  .brand__dot { border-radius: 50%; flex: none; }
  .card--front .brand { top: 34px; right: 30px; font-size: 24px; color: var(--ink); }
  .card--front .brand__dot { width: 14px; height: 14px; background: var(--blue-bright); }
  .card--back .brand {
    top: 50%; left: 50%; transform: translate(-50%, -50%);
    font-size: 32px; color: var(--blue);
  }
  .card--back .brand__dot { width: 18px; height: 18px; background: var(--blue-bright); }

  .abn {
    position: absolute; right: 30px; top: 118px;
    font-size: 12.5px; color: var(--blue-bright); letter-spacing: .2px;
  }
  .contacts {
    position: absolute; right: 30px; top: 150px;
    list-style: none; text-align: right;
  }
  .contacts li {
    display: flex; justify-content: flex-end; align-items: center; gap: 8px;
    font-size: 12.5px; color: var(--ink); line-height: 21px;
  }
  .contacts svg { width: 12px; height: 12px; flex: none; }

  .person { position: absolute; left: 34px; bottom: 30px; }
  .person__name { font-size: 26px; line-height: 1.1; font-weight: 500; color: var(--ink-soft); }
  .person__first { font-weight: 700; color: var(--blue-bright); }
  .person__role { font-size: 13px; color: var(--ink); margin-top: 4px; }
</style>
</head>
<body>

<section class="card card--front" aria-label="Business card front">
  <div class="corner-panel" role="img" aria-label="Decorative pale blue water curve area"></div>

  <div class="brand"><span class="brand__dot"></span>tbk plumbing services</div>

  <p class="abn">ABN - 73 215 904 386</p>
  <ul class="contacts">
    <li>0431 286 517
      <svg viewBox="0 0 12 12" aria-hidden="true"><circle cx="6" cy="6" r="6" fill="var(--blue-bright)"/><path d="M4 3 L5 3 L5.5 4.5 L4.8 5 Q5.5 6.6 7 7.2 L7.5 6.5 L9 7 L9 8 Q8.5 9 7.5 9 Q4 8.4 3 4.5 Q3 3.5 4 3 Z" fill="#fff"/></svg>
    </li>
    <li>rowan@tbk-plumbing.com.au
      <svg viewBox="0 0 12 12" aria-hidden="true"><circle cx="6" cy="6" r="6" fill="var(--blue-bright)"/><rect x="3" y="4" width="6" height="4.2" fill="#fff"/><path d="M3 4 L6 6.3 L9 4" fill="none" stroke="var(--blue-bright)" stroke-width=".8"/></svg>
    </li>
    <li>www.tbk-plumbing.com.au
      <svg viewBox="0 0 12 12" aria-hidden="true"><circle cx="6" cy="6" r="6" fill="var(--blue-bright)"/><circle cx="6" cy="6" r="3.3" fill="none" stroke="#fff" stroke-width=".8"/><path d="M2.7 6 H9.3 M6 2.7 V9.3" stroke="#fff" stroke-width=".8"/></svg>
    </li>
  </ul>

  <div class="person">
    <p class="person__name"><span class="person__first">Rowan</span> Keddle</p>
    <p class="person__role">Director</p>
  </div>
</section>

<section class="card card--back" aria-label="Business card back">
  <div class="brand"><span class="brand__dot"></span>tbk plumbing services</div>
</section>

</body>
</html>
```